Vantro cards

I am in the auto motive, transportation business I would like a business card that is Something cool, modern edgy, having to do with car culture. I offer towing service for high and exotic cars. I also provide towing for collisions and car accidents. I offer open and enclosed transport nationwide.

Target Market(s)

Car culture people high end auto collectors

Industry/Entity Type

Towing car carrier

Contact Information for Business Card

My company colors black yellow and silver

Font styles to use
Serif

```html
<!DOCTYPE html>
<html lang="en">
<head>
<meta charset="utf-8">
<title>Vantro Cards</title>
<link rel="stylesheet" href="https://fonts.googleapis.com/css2?family=Poppins:wght@400;500;600&display=swap">
<style>
  :root {
    --ink: #0a0a0a;
    --paper: #ffffff;
    --gold: #f9dc5c;
    --stage: #e9e9e7;
  }
  * { margin: 0; padding: 0; box-sizing: border-box; }
  html, body { width: 1200px; height: 900px; overflow: hidden; }
  body {
    background: var(--stage);
    font-family: "Poppins", sans-serif;
    position: relative;
  }
  .card {
    position: absolute;
    left: 250px;
    width: 700px;
    height: 400px;
    overflow: hidden;
    box-shadow: 0 6px 18px rgba(0,0,0,.18);
  }
  .card--back { top: 35px; background: var(--ink); }
  .card--front { top: 465px; background: var(--paper); }

  .brand {
    position: absolute;
    display: flex;
    align-items: center;
    gap: 14px;
    font-weight: 600;
    letter-spacing: .06em;
    text-transform: uppercase;
    z-index: 1;
  }
  .brand__dot { border-radius: 50%; background: var(--gold); flex: none; }
  .card--back .brand {
    left: 50%; top: 50%;
    transform: translate(-50%, -50%);
    color: var(--paper);
    font-size: 58px;
  }
  .card--back .brand__dot { width: 40px; height: 40px; }
  .card--front .brand {
    right: 70px; top: 95px;
    color: var(--ink);
    font-size: 44px;
  }
  .card--front .brand__dot { width: 30px; height: 30px; }

  .wave { position: absolute; inset: 0; width: 100%; height: 100%; }
  .wave__black { fill: var(--ink); }
  .wave__gold { fill: var(--gold); }

  .person { position: absolute; left: 60px; top: 90px; color: var(--ink); z-index: 1; }
  .person__name { font-weight: 600; font-size: 25px; letter-spacing: .02em; line-height: 1; }
  .person__role { font-weight: 400; font-size: 17px; letter-spacing: .03em; margin-top: 4px; }

  .contact {
    position: absolute; left: 60px; top: 172px;
    list-style: none; color: var(--ink);
    font-size: 18px; line-height: 1.4; letter-spacing: .02em;
    z-index: 1;
  }
  .contact li { display: flex; align-items: center; gap: 12px; }
  .contact svg { width: 22px; height: 22px; flex: none; }
  .contact__icon { fill: var(--gold); }
  .contact__address { margin-top: 8px; padding-left: 34px; line-height: 1.3; }

  .website {
    position: absolute; right: 40px; bottom: 70px;
    color: var(--gold); font-size: 17px; letter-spacing: .03em;
    z-index: 1;
  }
</style>
</head>
<body>
  <section class="card card--back" aria-label="Business card back">
    <div class="brand"><span class="brand__dot"></span>Vantro</div>
  </section>

  <section class="card card--front" aria-label="Business card front">
    <svg class="wave" viewBox="0 0 700 400" preserveAspectRatio="none" aria-hidden="true">
      <path class="wave__gold" d="M0,340 C170,342 330,305 460,232 C355,305 210,352 0,358 Z"/>
      <path class="wave__black" d="M0,358 C210,356 355,312 475,238 C572,178 640,150 700,140 L700,400 L0,400 Z"/>
    </svg>

    <div class="brand"><span class="brand__dot"></span>Vantro</div>

    <div class="person">
      <p class="person__name">MARCUS HALE</p>
      <p class="person__role">Managing Director</p>
    </div>

    <ul class="contact">
      <li>
        <svg viewBox="0 0 24 24" aria-hidden="true"><path class="contact__icon" d="M6.6 10.8a15.1 15.1 0 0 0 6.6 6.6l2.2-2.2a1 1 0 0 1 1-.25 11.4 11.4 0 0 0 3.6.57 1 1 0 0 1 1 1V20a1 1 0 0 1-1 1A17 17 0 0 1 3 4a1 1 0 0 1 1-1h3.5a1 1 0 0 1 1 1c0 1.25.2 2.45.57 3.57a1 1 0 0 1-.25 1z"/></svg>
        044-555 218 406
      </li>
      <li>
        <svg viewBox="0 0 24 24" aria-hidden="true"><path class="contact__icon" d="M2 5h20v14H2z M3.5 6.5 12 13l8.5-6.5" /></svg>
        info@vantrotow.com
      </li>
      <li class="contact__address">421, Address line here<br>Country Name, 45452</li>
    </ul>

    <p class="website">www.vantrotow.com</p>
  </section>
</body>
</html>
```